Business Card front and back

I am looking for business card design. I really really like the design file I uploaded named 627788_19250069_3478263_85f427ee_image

Target Market(s)

Corporate Fitness High end Private country club

Industry/Entity Type

Fitness Industry

Contact Information for Business Card

The last image I like as an example I uploaded a bunch of my logos. The file labeled "the signature" is my business card information for you to use

Colors
0054AA
0677BA
7BADD7
CADEEF
E8F1F8

Requirements
Must have
• E-mail sigThe file I uploaded labeled "627788_19250069_3478263_85f427ee_image" with all the plus signs on the back if those could be the logo symbol I uploaded labeled "1 back.png"

```html
<!DOCTYPE html>
<html lang="en">
<head>
<meta charset="utf-8">
<title>Stridewell Athletics – Business Card</title>
<link href="https://fonts.googleapis.com/css2?family=Lato:wght@400;700;900&display=swap" rel="stylesheet">
<style>
  :root {
    --page: #1b1b1c;
    --card: #2f2f30;
    --blue: #4a7fc4;
    --white: #f4f4f4;
    --silver: #a9a9ab;
    --muted: #3a3a3b;
  }
  * { margin: 0; padding: 0; box-sizing: border-box; }
  html, body {
    width: 1200px; height: 1122px; overflow: hidden;
    background: var(--page);
    font-family: "Lato", sans-serif;
  }
  .card {
    position: absolute; left: 190px;
    width: 820px; height: 470px;
    background: var(--card);
    border-radius: 30px;
    overflow: hidden;
    box-shadow: 0 18px 40px rgba(0,0,0,.45);
  }
  .card--back { top: 60px; }
  .card--front { top: 592px; }

  .brand-name {
    position: absolute; left: 0; right: 0;
    text-align: center;
    font-weight: 900; letter-spacing: 3px;
    text-transform: uppercase;
    white-space: nowrap;
  }
  .card--back .brand-name {
    top: 205px; font-size: 50px; color: var(--silver);
  }
  .card--front .brand-name {
    top: 90px; font-size: 40px; color: var(--white);
  }

  .person {
    position: absolute; top: 190px; right: 430px;
    text-align: right;
    white-space: nowrap;
  }
  .person__name {
    font-weight: 900; font-size: 40px; color: var(--blue);
    letter-spacing: .5px; text-transform: uppercase;
  }
  .person__role {
    font-size: 25px; color: var(--white); margin-top: 4px;
  }
  .divider {
    position: absolute; left: 412px; top: 196px;
    width: 2px; height: 110px; background: var(--blue);
  }
  .contacts {
    position: absolute; left: 440px; top: 196px;
    list-style: none;
  }
  .contacts li {
    display: flex; align-items: center; gap: 12px;
    color: var(--white); font-size: 21px; height: 36px;
    white-space: nowrap;
  }
  .contacts li.phone { font-weight: 700; font-size: 23px; }
  .contacts svg { width: 18px; height: 18px; fill: var(--blue); flex: none; }

  .region-band {
    position: absolute; left: 0; right: 0; top: 370px; height: 66px;
    background: var(--blue);
    display: flex; align-items: center;
    padding-left: 24px;
  }
  .region-band .corner-dot {
    width: 40px; height: 40px; border-radius: 50%;
    background: var(--muted); margin-right: 170px; flex: none;
  }
  .region-band .region {
    display: flex; align-items: center; gap: 12px;
    color: var(--white); font-size: 22px; letter-spacing: 1px;
    white-space: nowrap;
  }
  .region svg { width: 18px; height: 24px; fill: var(--white); flex: none; }
</style>
</head>
<body>

<section class="card card--back" aria-label="Card back">
  <p class="brand-name">Stridewell Athletics</p>
</section>

<section class="card card--front" aria-label="Card front">
  <p class="brand-name">Stridewell Athletics</p>

  <div class="person">
    <p class="person__name">Daniel Arvo</p>
    <p class="person__role">Consultant</p>
  </div>

  <span class="divider"></span>

  <ul class="contacts">
    <li class="phone">
      <svg viewBox="0 0 24 24"><path d="M6.6 10.8a15.1 15.1 0 0 0 6.6 6.6l2.2-2.2a1 1 0 0 1 1-.25 11.4 11.4 0 0 0 3.6.57 1 1 0 0 1 1 1V20a1 1 0 0 1-1 1A17 17 0 0 1 3 4a1 1 0 0 1 1-1h3.5a1 1 0 0 1 1 1c0 1.25.2 2.45.57 3.57a1 1 0 0 1-.25 1z"/></svg>
      555-014-2276
    </li>
    <li>
      <svg viewBox="0 0 24 24"><path d="M2 5h20v14H2z M2 5l10 8 10-8" fill="none" stroke="#4a7fc4" stroke-width="2"/></svg>
      daniel@stridewell.co
    </li>
    <li>
      <svg viewBox="0 0 24 24"><circle cx="12" cy="12" r="9" fill="none" stroke="#4a7fc4" stroke-width="2"/><path d="M3 12h18M12 3c3 3 3 15 0 18M12 3c-3 3-3 15 0 18" fill="none" stroke="#4a7fc4" stroke-width="1.6"/></svg>
      stridewell.co
    </li>
  </ul>

  <div class="region-band">
    <span class="corner-dot"></span>
    <p class="region">
      <svg viewBox="0 0 18 24"><path d="M9 0a9 9 0 0 0-9 9c0 6.5 9 15 9 15s9-8.5 9-15a9 9 0 0 0-9-9zm0 12.5A3.5 3.5 0 1 1 9 5.5a3.5 3.5 0 0 1 0 7z"/></svg>
      OR. WA. ID. MT. WY. UT
    </p>
  </div>
</section>

</body>
</html>
```